Transform Your Giving

I need a tri-fold brochure that will fit in a standard number 10 business envelope. Meadowlark and Allied Services is a charitable nonprofit. The goal of this brochure is to stimulate people into thinking about other ways to make a donation. The design should communicate the essential information on donation options, create a sense of professional integrity, be graphically sharp, easy to read and laid out in a way that doesn't make the material appear crowded.

```html
<!DOCTYPE html>
<html lang="en">
<head>
<meta charset="utf-8">
<title>Transform Your Giving – Tri-fold Brochure</title>
<link rel="stylesheet" href="https://fonts.googleapis.com/css2?family=Montserrat:ital,wght@0,400;0,600;0,700;0,800;1,600;1,700&family=Oswald:wght@500;600&display=swap">
<style>
:root{
  --navy:#23228a;
  --navy-dark:#1b1a6e;
  --green:#4ee01f;
  --green-dark:#3bb516;
  --white:#ffffff;
  --paper:#f3f4f7;
  --ink:#2a2a3a;
  --stage:#eceef2;
}
*{box-sizing:border-box;margin:0;padding:0}
html,body{width:1200px;height:2399px;overflow:hidden}
body{background:var(--stage);font-family:"Montserrat",sans-serif;color:var(--ink)}
.spread{position:absolute;left:30px;width:1140px;height:880px;display:flex;box-shadow:0 10px 30px rgba(20,20,60,.15)}
.spread--outside{top:200px}
.spread--inside{top:1319px}
.panel{position:relative;width:380px;height:880px;overflow:hidden;background:var(--white)}
.panel--navy{background:var(--navy);color:var(--white)}
.panel + .panel{border-left:1px solid rgba(0,0,0,.06)}
.shape{position:absolute;inset:0;width:380px;height:880px}
.photo{position:absolute;left:0;width:380px}
.content{position:relative;z-index:2;padding:0 30px}
.body-text{font-size:9px;line-height:1.45}
.title{font-family:"Oswald",sans-serif;text-transform:uppercase;letter-spacing:.5px}

/* cover */
.cover-head{position:absolute;top:54px;left:30px;right:24px;z-index:2}
.cover-title{font-size:38px;color:var(--green);line-height:1}
.cover-pill{display:inline-block;margin-top:8px;background:var(--navy);color:var(--white);font-weight:800;font-size:17px;padding:5px 16px;border-radius:16px;letter-spacing:.5px}
.cover-sub{margin-top:10px;font-size:14px;color:var(--ink);line-height:1.35}
.bubble{position:absolute;z-index:3;width:86px;height:86px;border-radius:50%;background:radial-gradient(circle at 35% 30%,rgba(255,255,255,.97),rgba(228,232,245,.85));box-shadow:0 4px 12px rgba(0,0,0,.15);display:flex;flex-direction:column;align-items:center;justify-content:center;color:var(--navy);font-size:9px;font-weight:700;text-align:center;line-height:1.1}
.bubble svg{margin-bottom:4px}
.brand{position:absolute;z-index:3;text-align:center;color:var(--navy)}
.brand-mark{display:flex;align-items:center;justify-content:center;gap:8px;font-weight:800;font-size:46px;letter-spacing:3px;line-height:1}
.brand-dot{width:14px;height:14px;border-radius:50%;background:var(--green)}
.brand-name{font-size:8.5px;font-weight:800;letter-spacing:.6px;margin-top:4px}

/* back panel */
.back-intro{padding-top:36px;text-align:center}
.quote{margin:26px 0 0;padding:14px 18px;border-top:2px solid var(--green);border-bottom:2px solid var(--green);border-radius:0 0 18px 0;font-style:italic;font-weight:600;font-size:13px;line-height:1.4}
.quote-mark{color:var(--green);font-size:34px;font-weight:800;line-height:.5;font-style:normal}
.quote-by{font-size:11px;font-weight:700;margin-top:4px}
.back-brand{position:relative;margin:30px auto 0;color:var(--white)}
.will-pill{margin:18px -6px 0;background:var(--green);color:var(--navy);border-radius:20px;padding:9px 14px;text-align:center;font-size:9.5px;font-weight:600;line-height:1.4}
.contact{text-align:center;margin-top:26px}
.contact h3{font-size:13px;font-weight:800;letter-spacing:1px;margin-bottom:6px}
.contact-row{display:flex;flex-direction:column;align-items:center;gap:3px;margin-top:10px;font-size:10px}
.icon-dot{width:16px;height:16px;border-radius:50%;background:var(--green);display:flex;align-items:center;justify-content:center}
.follow{text-align:center;margin-top:24px;font-size:12px;font-weight:800}
.social{display:flex;justify-content:center;gap:10px;margin-top:8px}
.social span{width:18px;height:18px;border-radius:50%;background:var(--green)}
.disclaimer{font-size:6.5px;line-height:1.4;text-align:center;margin-top:18px;opacity:.85}

/* impact panel */
.impact{position:absolute;top:478px;left:0;right:0;z-index:2}
.impact-banner{display:inline-block;background:var(--navy);color:var(--white);font-family:"Oswald",sans-serif;font-size:19px;padding:6px 30px 6px 30px;clip-path:polygon(0 0,100% 0,92% 100%,0 100%);text-transform:uppercase}
.impact .content{padding-top:16px}
.gift-list{list-style:none;margin-top:14px;font-size:10px;font-weight:700;color:var(--navy)}
.gift-list li{display:flex;align-items:center;gap:8px;margin-bottom:7px}
.gift-list li::before{content:"";width:9px;height:9px;border:1.5px solid var(--navy);border-radius:2px}

/* inside sections */
.option{margin-top:16px}
.option-head{display:flex;gap:10px;align-items:flex-start}
.option-title{font-size:12.5px;font-weight:800;color:var(--green);line-height:1.2}
.option-lead{font-size:9px;font-style:italic;font-weight:700;color:var(--green);line-height:1.3;margin-top:2px}
.panel--white .option-title{color:var(--green-dark)}
.panel--white .option-lead{color:var(--green-dark)}
.how-pill{display:inline-block;margin:10px 0 8px;background:var(--green);color:var(--navy);font-weight:800;font-size:10px;padding:4px 16px;border-radius:12px;letter-spacing:.5px}
.checks{list-style:none;margin-top:6px}
.checks li{display:flex;gap:7px;margin-bottom:6px}
.checks li svg{flex:none;margin-top:1px}
.site-pill{position:absolute;z-index:3;right:24px;bottom:24px;background:var(--navy);color:var(--white);font-size:11px;font-weight:700;padding:6px 18px;border-radius:14px}
</style>
</head>
<body>

<!-- OUTSIDE SPREAD -->
<section class="spread spread--outside">

  <!-- inside flap -->
  <article class="panel panel--white">
    <div class="photo" style="top:0;height:470px;background:linear-gradient(160deg,#d9d6d0,#b9b2a8 45%,#8a8278 75%,#c9c5bd)" role="img" aria-label="Photo of two young women laughing together on a sofa"></div>
    <svg class="shape" viewBox="0 0 380 880" aria-hidden="true">
      <path d="M0 452 Q240 430 380 340 V364 Q245 452 0 472 Z" fill="var(--green)"/>
      <path d="M0 472 Q245 452 380 364 V880 H0 Z" fill="var(--white)"/>
    </svg>
    <div class="impact">
      <div class="impact-banner">The Impact of Your Gift</div>
      <div class="content">
        <p class="body-text">Your generosity drives our mission. With every Smart gift you're supporting Meadowlark and Allied Services. Join our community of Smart donors today and make an enduring impact. With Smart Giving your generosity reaches further. Begin your Smart Giving journey with us today.</p>
        <ul class="gift-list">
          <li>Stocks and Securities</li>
          <li>DAFs</li>
          <li>QCDs</li>
          <li>Crypto</li>
          <li>Charitable Annuity</li>
        </ul>
      </div>
    </div>
  </article>

  <!-- back panel -->
  <article class="panel panel--navy">
    <div class="content">
      <p class="body-text back-intro">To learn more about Smart Giving Options and how they can benefit you and Meadowlark and Allied Services, please reach out to our team. We're here to help you navigate these giving methods and answer any question you may have.</p>
      <blockquote class="quote">
        <div class="quote-mark">&ldquo;</div>
        Being kind to others is a way of being good to yourself.
        <div class="quote-by">- Miriam Castell</div>
      </blockquote>
      <div class="brand back-brand" style="position:relative">
        <div class="brand-mark" style="font-size:38px"><span class="brand-dot"></span>MAS</div>
        <div class="brand-name">MEADOWLARK AND ALLIED SERVICES, INC.</div>
      </div>
      <p class="will-pill">If you do not have a will, go to <strong>www.easywillnow.org</strong><br>In 20 minutes you can have a legal will for free.</p>
      <div class="contact">
        <h3>CONTACT US</h3>
        <p class="body-text">Have more question?<br>Please contact us at Meadowlark &amp; Allied Services</p>
        <div class="contact-row">
          <span class="icon-dot"><svg width="8" height="10" viewBox="0 0 8 10"><path d="M4 0a4 4 0 0 1 4 4c0 3-4 6-4 6S0 7 0 4a4 4 0 0 1 4-4z" fill="var(--navy)"/></svg></span>
          <span>1420 Prairie Rose Ave,<br>Suite 4, Fargo Springs, ND 58000</span>
        </div>
        <div class="contact-row">
          <span class="icon-dot"><svg width="9" height="9" viewBox="0 0 10 10"><path d="M2 0l2 2-1 2a6 6 0 0 0 3 3l2-1 2 2-2 2C4 10 0 6 0 2z" fill="var(--navy)"/></svg></span>
          <span>555-014-6600 (ext. 100)</span>
        </div>
        <div class="contact-row">
          <span class="icon-dot"><svg width="10" height="8" viewBox="0 0 10 8"><rect width="10" height="8" rx="1" fill="var(--navy)"/><path d="M0 1l5 3 5-3" stroke="var(--green)" fill="none"/></svg></span>
          <span>jtallis@meadowlarkallied.org</span>
        </div>
        <div class="contact-row">
          <span>www.meadowlarkallied.org</span>
        </div>
      </div>
      <div class="follow">Follow us:
        <div class="social"><span></span><span></span><span></span></div>
      </div>
      <p class="disclaimer">This material has been prepared for informational purposes only and is not intended to provide tax, legal or financial advice. Please consult your own advisor before making any decision about Smart Giving.</p>
    </div>
  </article>

  <!-- cover -->
  <article class="panel panel--white">
    <div class="photo" style="top:230px;height:520px;background:linear-gradient(170deg,#cfcac4,#a89a8c 40%,#6e5a4a 60%,#c8c4be)" role="img" aria-label="Photo of a smiling woman with curly hair resting her face in her hands"></div>
    <svg class="shape" viewBox="0 0 380 880" aria-hidden="true">
      <path d="M0 318 Q230 312 380 222 V254 Q240 342 0 338 Z" fill="var(--green)"/>
      <path d="M0 0 H380 V222 Q230 312 0 318 Z" fill="var(--white)"/>
      <path d="M0 760 Q200 720 380 610 V640 Q210 745 0 786 Z" fill="var(--navy)"/>
      <path d="M0 786 Q210 745 380 640 V880 H0 Z" fill="var(--white)"/>
    </svg>
    <header class="cover-head">
      <h1 class="title cover-title">Transform Your Giving</h1>
      <div class="cover-pill">BE STRATEGIC, BE SMART</div>
      <p class="cover-sub">Discover the impact of Smart Giving with Meadowlark and Allied Services</p>
    </header>
    <div class="bubble" style="top:345px;left:26px">
      <svg width="30" height="18" viewBox="0 0 30 18"><circle cx="9" cy="9" r="8" fill="none" stroke="var(--navy)" stroke-width="2"/><circle cx="21" cy="9" r="8" fill="none" stroke="var(--navy)" stroke-width="2"/></svg>Crypto</div>
    <div class="bubble" style="top:300px;left:268px">
      <svg width="30" height="22" viewBox="0 0 30 22"><circle cx="10" cy="12" r="8" fill="none" stroke="var(--navy)" stroke-width="2"/><circle cx="21" cy="9" r="7" fill="none" stroke="var(--navy)" stroke-width="2"/></svg>DAF's</div>
    <div class="bubble" style="top:470px;left:48px">
      <svg width="26" height="22" viewBox="0 0 26 22"><rect x="2" y="12" width="4" height="10" fill="var(--navy)"/><rect x="9" y="7" width="4" height="15" fill="var(--navy)"/><rect x="16" y="10" width="4" height="12" fill="var(--navy)"/><path d="M1 8 L9 3 L15 6 L25 0" stroke="var(--navy)" stroke-width="2" fill="none"/></svg>Stocks &amp;<br>Securities</div>
    <div class="bubble" style="top:500px;left:272px">
      <svg width="24" height="24" viewBox="0 0 24 24"><rect x="2" y="9" width="20" height="14" fill="var(--navy)"/><rect x="0" y="5" width="24" height="5" fill="var(--navy)"/><rect x="11" y="5" width="2" height="18" fill="#fff"/></svg>QCDs</div>
    <div class="bubble" style="top:620px;left:40px">
      <svg width="26" height="24" viewBox="0 0 26 24"><circle cx="18" cy="5" r="4" fill="var(--navy)"/><rect x="2" y="16" width="14" height="3" rx="1" fill="var(--navy)"/><rect x="2" y="20" width="14" height="3" rx="1" fill="var(--navy)"/><rect x="4" y="12" width="14" height="3" rx="1" fill="var(--navy)"/></svg>Charitable<br>Annuity</div>
    <div class="brand" style="left:0;right:0;bottom:38px">
      <div class="brand-mark"><span class="brand-dot"></span>MAS</div>
      <div class="brand-name">MEADOWLARK AND ALLIED SERVICES, INC.</div>
    </div>
  </article>
</section>

<!-- INSIDE SPREAD -->
<section class="spread spread--inside">

  <!-- stocks & DAF -->
  <article class="panel panel--navy">
    <div class="photo" style="top:770px;height:110px;background:linear-gradient(180deg,#f4c067,#d9853a 55%,#5a3a2a)" role="img" aria-label="Photo of a family running on a beach at sunset"></div>
    <svg class="shape" viewBox="0 0 380 880" aria-hidden="true">
      <path d="M0 760 Q200 748 380 770 V778 Q200 760 0 782 Z" fill="var(--green)"/>
      <path d="M0 782 Q200 760 380 778 V790 Q200 772 0 792 Z" fill="var(--white)"/>
    </svg>
    <div class="content" style="padding-top:34px">
      <p class="body-text">We would like to introduce you to five Strategic and Smart ways to give that could potentially be more beneficial to you compared to traditional cash donations. We encourage you to keep this information as a guide for your future contributions.</p>
      <div class="option">
        <div class="option-head">
          <svg width="36" height="30" viewBox="0 0 36 30" aria-hidden="true"><rect x="2" y="16" width="6" height="14" fill="var(--green)"/><rect x="11" y="10" width="6" height="20" fill="var(--green)"/><rect x="20" y="14" width="6" height="16" fill="var(--green)"/><rect x="29" y="6" width="6" height="24" fill="var(--green)"/><path d="M1 12 L12 4 L20 8 L35 0" stroke="var(--white)" stroke-width="2" fill="none"/></svg>
          <div>
            <h2 class="option-title">Gifts of Stocks or Appreciated Assets Strategic &amp; Smart</h2>
            <p class="option-lead">Consider your long-term publicly traded stock as a way to give to your favorite charity.</p>
          </div>
        </div>
        <p class="body-text" style="margin-top:8px">You can make a significantly bigger impact when you donate long-term appreciated securities, including stock, mutual funds, and bonds, directly to your favorite charity.</p>
        <span class="how-pill">HOW DOES IT WORK?</span>
        <p class="body-text">When you donate stock to a charity, you will generally take a tax deduction for the full market value. Because you are donating stock, your contribution and tax deduction may be significantly higher than contributing the after-tax proceeds. The same benefits apply when you donate mutual funds or bonds.</p>
      </div>
      <div class="option">
        <div class="option-head">
          <svg width="36" height="30" viewBox="0 0 36 30" aria-hidden="true"><circle cx="13" cy="17" r="11" fill="none" stroke="var(--green)" stroke-width="3"/><circle cx="27" cy="10" r="8" fill="none" stroke="var(--green)" stroke-width="3"/></svg>
          <div>
            <h2 class="option-title">Donor-Advised Fund (DAF) Strategic &amp; Smart</h2>
            <p class="option-lead">Consider a DAF – a simple, flexible, and tax-advantageous way to give to your favorite charities.</p>
          </div>
        </div>
        <p class="body-text" style="margin-top:8px">A Donor-Advised Fund (DAF) is like a charitable investment account for the sole purpose of supporting your favorite charities.</p>
        <span class="how-pill">HOW DOES IT WORK?</span>
        <p class="body-text">You establish a DAF and contribute cash, stocks, or non-publicly traded assets, cryptocurrency, and private company stock to be eligible for an immediate tax deduction. Those funds are contributed for tax-free growth. You can recommend grants be made from your DAF to any IRS qualified public charity.</p>
      </div>
    </div>
  </article>

  <!-- QCDs -->
  <article class="panel panel--white">
    <div class="photo" style="top:0;height:440px;background:linear-gradient(180deg,#eef1f4,#cfd8d8 50%,#7f9a86 80%,#5d7a63)" role="img" aria-label="Photo of a happy family flying a rainbow kite outdoors"></div>
    <svg class="shape" viewBox="0 0 380 880" aria-hidden="true">
      <path d="M0 412 Q210 432 380 352 V880 H0 Z" fill="var(--white)"/>
    </svg>
    <div class="content" style="padding-top:450px">
      <div class="option-head">
        <svg width="40" height="38" viewBox="0 0 24 24" aria-hidden="true"><rect x="2" y="9" width="20" height="14" fill="var(--green)"/><rect x="0" y="5" width="24" height="5" fill="var(--green)"/><rect x="11" y="5" width="2" height="18" fill="#fff"/><path d="M12 5 C8 0 5 3 8 5 M12 5 C16 0 19 3 16 5" stroke="var(--green)" stroke-width="2" fill="none"/></svg>
        <div>
          <h2 class="option-title">Qualified Charitable Distributions (QCDs) Strategic &amp; Smart</h2>
          <p class="option-lead">Consider a QCD – when planning your IRA withdrawal strategy...and donate to your favorite charity.</p>
        </div>
      </div>
      <p class="body-text" style="margin-top:8px">IRA owners at age 70 or over can transfer dollars from their IRA to charity tax-free each year. These transfers, known as Qualified Charitable Distributions (QCDs) offer eligible older Americans a great way to easily give to charity.</p>
      <span class="how-pill">HOW DOES IT WORK?</span>
      <p class="body-text">Are you 72 and required to take a minimum distribution (RMD) from your IRA but do not need the funds? Consider a Qualified Charitable Distribution. Normally, distributions from a traditional IRA are taxable when received. With a QCD, these distributions become tax-free when paid directly from the IRA to your favorite eligible charity. An IRA owner wishing to make a QCD should contact their IRA trustee, allowing time to complete the transfer before the end of the year to receive the tax benefit.</p>
    </div>
  </article>

  <!-- crypto & annuity -->
  <article class="panel panel--navy">
    <svg class="shape" viewBox="0 0 380 880" aria-hidden="true">
      <path d="M0 838 Q220 820 380 752 V770 Q225 838 0 852 Z" fill="var(--green)"/>
      <path d="M0 852 Q225 838 380 770 V880 H0 Z" fill="var(--white)"/>
    </svg>
    <div class="content" style="padding-top:30px">
      <div class="option-head">
        <svg width="36" height="24" viewBox="0 0 36 24" aria-hidden="true"><circle cx="11" cy="12" r="10" fill="none" stroke="var(--green)" stroke-width="3"/><circle cx="25" cy="12" r="10" fill="none" stroke="var(--green)" stroke-width="3"/></svg>
        <div>
          <h2 class="option-title">Cryptocurrency Strategic &amp; Smart</h2>
          <p class="option-lead">Consider donating Bitcoin and other cryptocurrencies to your favorite charity.</p>
        </div>
      </div>
      <p class="body-text" style="margin-top:8px">Bitcoin and other cryptocurrencies can be donated to charity just like other appreciated assets such as stocks and other business interests. Before you sell bitcoin and donate the after-tax proceeds, consider donating your bitcoin directly to a favorite charity.</p>
      <span class="how-pill">HOW DOES IT WORK?</span>
      <p class="body-text">Many donors find it useful to open a Donor-Advised Fund (DAF). This strategy includes two significant benefits, both for you and your favorite charity:</p>
      <ul class="checks body-text">
        <li><svg width="9" height="9" viewBox="0 0 10 10"><rect x=".5" y=".5" width="9" height="9" fill="none" stroke="#fff"/><path d="M2 5l2 2 4-5" stroke="var(--green)" stroke-width="1.5" fill="none"/></svg><span>Your tax deduction will be equal to the fair market value of the donated Bitcoin (as determined by a qualified appraisal).</span></li>
        <li><svg width="9" height="9" viewBox="0 0 10 10"><rect x=".5" y=".5" width="9" height="9" fill="none" stroke="#fff"/><path d="M2 5l2 2 4-5" stroke="var(--green)" stroke-width="1.5" fill="none"/></svg><span>Your cryptocurrency donation is tax-smart because you may eliminate capital gains taxes on the value appreciation AND your favorite charity will receive 100% of the value of the contribution.</span></li>
      </ul>
      <p class="body-text">Often charities are not able to accept direct donations of bitcoin, so using a DAF is a great way to donate these assets.</p>
      <div class="option">
        <div class="option-head">
          <svg width="36" height="32" viewBox="0 0 26 24" aria-hidden="true"><circle cx="18" cy="5" r="4" fill="var(--green)"/><rect x="2" y="16" width="14" height="3" rx="1" fill="var(--green)"/><rect x="2" y="20" width="14" height="3" rx="1" fill="var(--green)"/><rect x="4" y="12" width="14" height="3" rx="1" fill="var(--green)"/></svg>
          <div>
            <h2 class="option-title">Charitable Gift Annuity Strategic &amp; Smart</h2>
            <p class="option-lead">Consider establishing a Charitable Gift Annuity</p>
          </div>
        </div>
        <p class="body-text" style="margin-top:8px">You make a donation to a single charity. The gift is set aside in a reserve account and invested.</p>
        <span class="how-pill">HOW DOES IT WORK?</span>
        <p class="body-text">A charitable gift annuity is a contract between a donor and a charity. As a donor, you make a sizable gift to the charity using cash, securities, or possibly other assets. In return, you become eligible to take a partial tax deduction for your donation, plus you receive a fixed stream of income from the charity for the rest of your life. At the end of your life (as well as your spouse's if you're giving as a couple), the charity receives the remainder of the gift.</p>
      </div>
    </div>
    <div class="site-pill">www.meadowlarkallied.org</div>
  </article>
</section>

</body>
</html>
```